TINPAILFOLK.COM NEEDS FACELIFT!!!

Please see www.tinpailfolk.com for the basics. I am a glass artist who sells to retail market (art shows and e-commerce) as well as wholsale to art galleries nation wide. My site needs to serve both types of customer. I did the basics years ago, but now it's old and outdated . I need to totally rework the site, adding functionality as well as a new look.
My criteria are:
1. Need e-commerce page (cart) that allows for the rapid uploading of new artwork for my retail market.
2. Need separate login/e-commerce page for my wholesale customers as well as different pricing.
3. Need zip code lookup to show locations of current galleries.
4. Need registration page to collect customer emails/addresses for net marketing (brisk bulletin).
5. Design should be neutral background since I want to highlight to vivid colors of my work.
6. Site should be easy to navigate.
7. I need to have control of adding content to site as needed (new photos, events, etc.)
8. Need page to list upcoming schedule and event dates.
9. Need all the pages and content from old site, with some revisions to be determined after general design is complete.
...Any suggestions on how to make my site more interesting and functional are welcomed!!
Updates
Added photos of newer work today, some of these should appear in high impact areas of the site,. DEan
Question to all...I just remembered that I have already search engine optimized my site using all the appropriate meta tags and photo names, text, etc. for the search terms "glass boxes" and "mosaic mirrors." I am number 1 in zoppo search results of these terms. I need this to not change. Will redesigning my site affect this?
Reason: Hello all, I am in Rome italy right now on business and I have not had time to work with any of you on the designs yet. I am extending the deadline so I can provide more interaction . Dean
Reason: I am still traveling abroad and have no time to work with and review designs. I will be home on the 26th of Oct. then I will be more in touch. Dean
Target Market(s)
mid to high income women
Industry/Entity Type
E-Commerce
Requirements
Must have
- Separate shopping carts for retail and wholesale customers. Wholesale section requires login page.
Lots of pictures of my work. (will supply)
ZIP locator
Broken box repairs page. Customer describes broken piece and can buy replacement part. (size, color, knob color. Can provide pics of all the choices.)
Customer registration page to collect address and email for brisk bulletin or direct mailing.
I like a black or dark gray background of some sort, unless you have a better idea to make my work stand out
Nice to have
- Some kind of link in to social media sites would be great!!!
Should not have
- keep the layout very simple and easy to navigate. Don't want a confusing page

```html
<!DOCTYPE html>
<html lang="en">
<head>
<meta charset="utf-8">
<title>Tinpail Folk – Glass Boxes</title>
<link rel="stylesheet" href="https://fonts.googleapis.com/css2?family=Arimo:wght@400;700&family=Marcellus&display=swap">
<style>
:root{
  --ink:#111;
  --text:#333;
  --muted:#666;
  --logo:#3a3a3a;
  --maroon:#5c0a2c;
  --bar:#333;
  --line:#cfcfcf;
  --field:#e2e2e2;
  --white:#fff;
  --sky:#e9eaec;
}
*{box-sizing:border-box;margin:0;padding:0}
html,body{width:716px;height:1200px;overflow:hidden}
body{position:relative;background:var(--white);font-family:"Arimo",Arial,sans-serif;color:var(--text)}
.abs{position:absolute}
a{color:inherit}

/* header */
.brand{left:20px;top:12px;font-size:50px;font-weight:700;color:var(--logo);letter-spacing:-1.5px}
.cart-status{left:516px;top:26px;font-size:9px;color:var(--ink);display:flex;align-items:center;gap:3px}
.cart-status b{color:var(--maroon);font-size:11px}
.account-links{right:21px;top:48px;font-size:9px;color:var(--ink)}

.main-nav{left:22px;top:77px;width:671px;height:32px;border:1px solid #bdbdbd;border-radius:3px;
  background:linear-gradient(#fff,#ececec);display:flex;box-shadow:0 1px 2px rgba(0,0,0,.15);z-index:2}
.main-nav a{font-size:9px;font-weight:700;text-decoration:none;color:var(--ink);display:flex;align-items:center;justify-content:center;border-right:1px solid var(--line)}
.main-nav a:last-child{border-right:0}

/* hero */
.hero-sky{left:0;top:109px;width:716px;height:300px;background:radial-gradient(ellipse at 55% 40%,#fafafa 0%,var(--sky) 55%,#dcdde0 100%)}
.hero-photo{left:0;top:110px;width:300px;height:235px;background:linear-gradient(120deg,#c9cdd0 0%,#eef0f1 40%,#d9b3bb 70%,#8f8676 100%);border-radius:0 0 40px 0}
.hero-title{left:363px;top:124px;font-family:"Marcellus",Georgia,serif;font-size:50px;color:var(--maroon)}
.hero-copy{left:363px;top:196px;width:300px;font-size:11px;line-height:27px;color:var(--ink)}
.btn{background:var(--maroon);color:var(--white);font-size:9px;display:flex;align-items:center;justify-content:center;text-decoration:none}
.hero-more{left:575px;top:298px;width:75px;height:23px}

/* content panel */
.panel{left:22px;top:334px;width:671px;height:791px;background:var(--white);border:1px solid #c8c8c8;border-radius:4px;box-shadow:0 1px 4px rgba(0,0,0,.2)}
.card{border:1px solid var(--line);border-radius:4px;background:var(--white)}
.promo{top:343px;width:212px;height:147px}
.promo-img{position:absolute;left:6px;top:6px;width:97px;height:129px;background:#000}
.promo-body{position:absolute;left:108px;top:32px;width:98px;font-size:9px;color:var(--ink);line-height:1.3}
.promo-body h3{font-size:9.5px;font-weight:700;margin-bottom:8px}
.promo-body p{margin-bottom:8px}
.promo-body .price{color:var(--maroon)}
.promo-link{position:absolute;right:10px;bottom:15px;font-family:Georgia,serif;font-size:8.5px;color:var(--ink)}

.register{left:474px;top:343px;width:212px;height:147px}
.register h3{position:absolute;left:18px;top:9px;font-size:15px;font-weight:400;color:var(--ink)}
.field{position:absolute;height:24px;background:var(--field);border:1px solid #c4c4c4;font-size:10px;color:var(--muted);padding-left:8px;display:flex;align-items:center}

/* sidebar */
.side-head{left:29px;width:211px;height:31px;background:var(--bar);border-radius:4px;color:var(--white);font-size:11.5px;display:flex;align-items:center;justify-content:center}
.events{left:29px;top:541px;width:211px;height:225px}
.event{position:absolute;left:8px;width:195px;height:43px;display:flex;align-items:center;gap:8px;border-bottom:1px solid #ddd}
.event:last-child{border-bottom:0}
.event p{font-size:8.5px;line-height:14px;color:var(--text)}
.newsletter{left:29px;top:813px;width:211px;height:96px}
.map{left:29px;top:955px;width:211px;height:98px;border-radius:4px;background:linear-gradient(135deg,#ece8dc,#f4f1e8 50%,#e7e2d3)}
.connect{left:43px;top:1077px;font-size:11px;color:var(--ink)}
.social{top:1070px;width:26px;height:26px;border-radius:4px;background:#777;color:var(--white);font-size:6.5px;display:flex;align-items:center;justify-content:center}

/* products */
.products{left:252px;top:502px;display:grid;grid-template-columns:repeat(3,126px);column-gap:27px;row-gap:8px}
.product{height:200px}
.product-img{width:126px;height:126px;border:1px solid #ddd}
.product p{font-size:8.5px;line-height:13px;color:var(--text);margin:3px 0 0 3px}
.product .price{font-size:11px;font-weight:700;color:var(--ink);margin:4px 0 0 6px}
.product .actions{display:flex;justify-content:space-between;align-items:flex-end;margin:3px 2px 0 5px;font-size:8.5px}
.product .detail{color:var(--maroon)}
.product .add{display:flex;align-items:flex-end;gap:2px;color:var(--ink)}

/* footer */
.footer-nav{left:0;top:1147px;width:716px;text-align:center;font-size:9px;color:var(--text)}
.copyright{left:0;top:1170px;width:716px;text-align:center;font-size:8.5px;color:var(--text)}
</style>
</head>
<body>

<header>
  <div class="abs brand">Tinpail Folk</div>
  <div class="abs cart-status">
    <svg width="15" height="12" viewBox="0 0 15 12" aria-hidden="true"><path d="M0 1h3l2 7h8l1.5-5H4" fill="none" stroke="#111" stroke-width="1.2"/><circle cx="6" cy="10.5" r="1.2" fill="#111"/><circle cx="12" cy="10.5" r="1.2" fill="#111"/></svg>
    Shopping Cart: Now in your cart <b>( 0 )</b> items
  </div>
  <div class="abs account-links">My wish List | My Account</div>
  <nav class="abs main-nav">
    <a style="width:50px">Home</a>
    <a style="width:85px">About the Artist</a>
    <a style="width:68px">Glass Boxes</a>
    <a style="width:50px">Mosaic</a>
    <a style="width:72px">Other Photos</a>
    <a style="width:76px">Store Locator</a>
    <a style="width:70px">Shop Online</a>
    <a style="width:80px">Show Schedule</a>
    <a style="width:60px">Wholesale</a>
    <a style="width:58px">Contact</a>
  </nav>
</header>

<section>
  <div class="abs hero-sky"></div>
  <div class="abs hero-photo" role="img" aria-label="Heart-shaped clear and pink glass jewelry box with beaded metal trim"></div>
  <h1 class="abs hero-title">Lorem Ipsum</h1>
  <p class="abs hero-copy">&nbsp;It was popularised in the 1960s with the release of Typecraft sheets containing Lorem Ipsum passages, and more recently with desktop publishing software like Pagesmith Studio including versions of Lorem Ipsum.</p>
  <a class="abs btn hero-more">read more</a>
</section>

<main>
  <div class="abs panel"></div>

  <div class="abs card promo" style="left:29px">
    <div class="promo-img" role="img" aria-label="Oval mosaic mirror with pink glass border"></div>
    <div class="promo-body">
      <h3>Perfect for Bathroom,</h3>
      <p>Hall or Foyer</p>
      <p class="price">$100-$1500</p>
      <p>Ships in 1-4 weeks</p>
    </div>
    <a class="promo-link">CLICK HERE</a>
  </div>

  <div class="abs card promo" style="left:251px">
    <div class="promo-img" role="img" aria-label="White glass gift box with black ornamental detail"></div>
    <div class="promo-body">
      <h3>Great, Unique Gift Ideas!</h3>
      <p class="price">from $25!</p>
      <p>Same day shipping!</p>
    </div>
    <a class="promo-link">CLICK HERE</a>
  </div>

  <form class="abs card register">
    <h3>Registration Box</h3>
    <div class="field" style="left:10px;top:31px;width:195px">Name</div>
    <div class="field" style="left:10px;top:60px;width:195px">Email</div>
    <div class="field" style="left:10px;top:89px;width:195px">Password</div>
    <a class="abs btn" style="left:75px;top:119px;width:61px;height:19px">Submit</a>
  </form>

  <aside>
    <div class="abs side-head" style="top:503px">Upcoming schedule and Event</div>
    <div class="abs card events">
      <div class="event" style="top:6px"><svg width="35" height="35" viewBox="0 0 35 35" aria-hidden="true"><rect x="1" y="4" width="33" height="30" rx="3" fill="#111"/><rect x="5" y="13" width="25" height="17" fill="#fff"/><rect x="8" y="1" width="3" height="7" fill="#111"/><rect x="24" y="1" width="3" height="7" fill="#111"/><text x="17.5" y="27" font-size="12" font-family="Arimo,sans-serif" text-anchor="middle" fill="#111">12</text></svg><p>Lorem Ipsum is simply dummy text of the printing and typesetting industry.</p></div>
      <div class="event" style="top:49px"><svg width="35" height="35" viewBox="0 0 35 35" aria-hidden="true"><rect x="1" y="4" width="33" height="30" rx="3" fill="#111"/><rect x="5" y="13" width="25" height="17" fill="#fff"/><rect x="8" y="1" width="3" height="7" fill="#111"/><rect x="24" y="1" width="3" height="7" fill="#111"/><text x="17.5" y="27" font-size="12" font-family="Arimo,sans-serif" text-anchor="middle" fill="#111">12</text></svg><p>Lorem Ipsum is simply dummy text of the printing and typesetting industry.</p></div>
      <div class="event" style="top:92px"><svg width="35" height="35" viewBox="0 0 35 35" aria-hidden="true"><rect x="1" y="4" width="33" height="30" rx="3" fill="#111"/><rect x="5" y="13" width="25" height="17" fill="#fff"/><rect x="8" y="1" width="3" height="7" fill="#111"/><rect x="24" y="1" width="3" height="7" fill="#111"/><text x="17.5" y="27" font-size="12" font-family="Arimo,sans-serif" text-anchor="middle" fill="#111">12</text></svg><p>Lorem Ipsum is simply dummy text of the printing and typesetting industry.</p></div>
      <div class="event" style="top:135px"><svg width="35" height="35" viewBox="0 0 35 35" aria-hidden="true"><rect x="1" y="4" width="33" height="30" rx="3" fill="#111"/><rect x="5" y="13" width="25" height="17" fill="#fff"/><rect x="8" y="1" width="3" height="7" fill="#111"/><rect x="24" y="1" width="3" height="7" fill="#111"/><text x="17.5" y="27" font-size="12" font-family="Arimo,sans-serif" text-anchor="middle" fill="#111">12</text></svg><p>Lorem Ipsum is simply dummy text of the printing and typesetting industry.</p></div>
      <div class="event" style="top:178px"><svg width="35" height="35" viewBox="0 0 35 35" aria-hidden="true"><rect x="1" y="4" width="33" height="30" rx="3" fill="#111"/><rect x="5" y="13" width="25" height="17" fill="#fff"/><rect x="8" y="1" width="3" height="7" fill="#111"/><rect x="24" y="1" width="3" height="7" fill="#111"/><text x="17.5" y="27" font-size="12" font-family="Arimo,sans-serif" text-anchor="middle" fill="#111">12</text></svg><p>Lorem Ipsum is simply dummy text of the printing and typesetting industry.</p></div>
    </div>

    <div class="abs side-head" style="top:775px">News Letter</div>
    <form class="abs card newsletter">
      <div class="field" style="left:8px;top:7px;width:195px">Your email here</div>
      <div class="field" style="left:8px;top:35px;width:195px">Password</div>
      <a class="abs btn" style="left:74px;top:69px;width:62px;height:19px">Subscribe</a>
    </form>

    <div class="abs side-head" style="top:918px">Store Locator</div>
    <div class="abs map" role="img" aria-label="Street map showing the gallery location with a red pin"></div>

    <div class="abs connect">Connect us in</div>
    <a class="abs social" style="left:124px">Chatter</a>
    <a class="abs social" style="left:160px">Peeps</a>
    <a class="abs social" style="left:196px">Feed</a>
  </aside>

  <section class="abs products">
    <article class="product"><div class="product-img" role="img" aria-label="Stacked patterned glass drawer box" style="background:linear-gradient(160deg,#5a6a6e,#2a3a4a 50%,#6a4a2a)"></div><p>Lorem Ipsum is simply dummy text of the printing.</p><div class="price">$ 150.00</div><div class="actions"><a class="detail">detail</a><a class="add"><svg width="15" height="12" viewBox="0 0 15 12" aria-hidden="true"><path d="M0 1h3l2 7h8l1.5-5H4" fill="none" stroke="#111" stroke-width="1.2"/><circle cx="6" cy="10.5" r="1.2" fill="#111"/><circle cx="12" cy="10.5" r="1.2" fill="#111"/></svg>add to cart</a></div></article>
    <article class="product"><div class="product-img" role="img" aria-label="Plaid glass box on green legs" style="background:linear-gradient(160deg,#f4f4f4,#6a7ab8 45%,#8bc34a)"></div><p>Lorem Ipsum is simply dummy text of the printing.</p><div class="price">$ 150.00</div><div class="actions"><a class="detail">detail</a><a class="add"><svg width="15" height="12" viewBox="0 0 15 12" aria-hidden="true"><path d="M0 1h3l2 7h8l1.5-5H4" fill="none" stroke="#111" stroke-width="1.2"/><circle cx="6" cy="10.5" r="1.2" fill="#111"/><circle cx="12" cy="10.5" r="1.2" fill="#111"/></svg>add to cart</a></div></article>
    <article class="product"><div class="product-img" role="img" aria-label="Tower of colourful glass drawer boxes" style="background:linear-gradient(160deg,#1a2a3a,#3a8aa8 50%,#c8a040)"></div><p>Lorem Ipsum is simply dummy text of the printing.</p><div class="price">$ 150.00</div><div class="actions"><a class="detail">detail</a><a class="add"><svg width="15" height="12" viewBox="0 0 15 12" aria-hidden="true"><path d="M0 1h3l2 7h8l1.5-5H4" fill="none" stroke="#111" stroke-width="1.2"/><circle cx="6" cy="10.5" r="1.2" fill="#111"/><circle cx="12" cy="10.5" r="1.2" fill="#111"/></svg>add to cart</a></div></article>
    <article class="product"><div class="product-img" role="img" aria-label="Stack of vivid glass drawer boxes" style="background:linear-gradient(160deg,#1a2036,#3a7ab8 50%,#d06030)"></div><p>Lorem Ipsum is simply dummy text of the printing.</p><div class="price">$ 150.00</div><div class="actions"><a class="detail">detail</a><a class="add"><svg width="15" height="12" viewBox="0 0 15 12" aria-hidden="true"><path d="M0 1h3l2 7h8l1.5-5H4" fill="none" stroke="#111" stroke-width="1.2"/><circle cx="6" cy="10.5" r="1.2" fill="#111"/><circle cx="12" cy="10.5" r="1.2" fill="#111"/></svg>add to cart</a></div></article>
    <article class="product"><div class="product-img" role="img" aria-label="Cluster of colourful glass drawer boxes" style="background:linear-gradient(160deg,#1a2036,#4a8ac0 50%,#b04030)"></div><p>Lorem Ipsum is simply dummy text of the printing.</p><div class="price">$ 150.00</div><div class="actions"><a class="detail">detail</a><a class="add"><svg width="15" height="12" viewBox="0 0 15 12" aria-hidden="true"><path d="M0 1h3l2 7h8l1.5-5H4" fill="none" stroke="#111" stroke-width="1.2"/><circle cx="6" cy="10.5" r="1.2" fill="#111"/><circle cx="12" cy="10.5" r="1.2" fill="#111"/></svg>add to cart</a></div></article>
    <article class="product"><div class="product-img" role="img" aria-label="Tall stack of glass drawer boxes" style="background:linear-gradient(160deg,#1a2036,#4a9ab0 50%,#d07030)"></div><p>Lorem Ipsum is simply dummy text of the printing.</p><div class="price">$ 150.00</div><div class="actions"><a class="detail">detail</a><a class="add"><svg width="15" height="12" viewBox="0 0 15 12" aria-hidden="true"><path d="M0 1h3l2 7h8l1.5-5H4" fill="none" stroke="#111" stroke-width="1.2"/><circle cx="6" cy="10.5" r="1.2" fill="#111"/><circle cx="12" cy="10.5" r="1.2" fill="#111"/></svg>add to cart</a></div></article>
    <article class="product"><div class="product-img" role="img" aria-label="Teal glass drawer boxes stacked on red backdrop" style="background:linear-gradient(160deg,#2a1012,#3a8a90 50%,#6a2020)"></div><p>Lorem Ipsum is simply dummy text of the printing.</p><div class="price">$ 150.00</div><div class="actions"><a class="detail">detail</a><a class="add"><svg width="15" height="12" viewBox="0 0 15 12" aria-hidden="true"><path d="M0 1h3l2 7h8l1.5-5H4" fill="none" stroke="#111" stroke-width="1.2"/><circle cx="6" cy="10.5" r="1.2" fill="#111"/><circle cx="12" cy="10.5" r="1.2" fill="#111"/></svg>add to cart</a></div></article>
    <article class="product"><div class="product-img" role="img" aria-label="Earth-toned glass drawer boxes" style="background:linear-gradient(160deg,#2a2a2a,#7a6a48 50%,#4a5a40)"></div><p>Lorem Ipsum is simply dummy text of the printing.</p><div class="price">$ 150.00</div><div class="actions"><a class="detail">detail</a><a class="add"><svg width="15" height="12" viewBox="0 0 15 12" aria-hidden="true"><path d="M0 1h3l2 7h8l1.5-5H4" fill="none" stroke="#111" stroke-width="1.2"/><circle cx="6" cy="10.5" r="1.2" fill="#111"/><circle cx="12" cy="10.5" r="1.2" fill="#111"/></svg>add to cart</a></div></article>
    <article class="product"><div class="product-img" role="img" aria-label="Tall green glass tower with drawers" style="background:linear-gradient(160deg,#0a0a0a,#4a5a4a 50%,#1a1a1a)"></div><p>Lorem Ipsum is simply dummy text of the printing.</p><div class="price">$ 150.00</div><div class="actions"><a class="detail">detail</a><a class="add"><svg width="15" height="12" viewBox="0 0 15 12" aria-hidden="true"><path d="M0 1h3l2 7h8l1.5-5H4" fill="none" stroke="#111" stroke-width="1.2"/><circle cx="6" cy="10.5" r="1.2" fill="#111"/><circle cx="12" cy="10.5" r="1.2" fill="#111"/></svg>add to cart</a></div></article>
  </section>
</main>

<footer>
  <nav class="abs footer-nav">Home &nbsp;|&nbsp; About the Artist &nbsp;|&nbsp; Glass Boxes &nbsp;|&nbsp; Mosaic &nbsp;|&nbsp; Other Photos &nbsp;|&nbsp; Store Locator &nbsp;|&nbsp; Shop Online &nbsp;|&nbsp; Show Schedule &nbsp;|&nbsp; Wholesale &nbsp;|&nbsp; Contact</nav>
  <p class="abs copyright">All Copyrights.Tinpailfolk.reserved</p>
</footer>

</body>
</html>
```